QVR business card

Need a business card for a company that provides instructional design and elearning development services. The website is here: http://quorvane.studio/

I'm attaching a current logo, as well as the old business card design. While I like to keep it clean, the old design is too simplistic for my liking. The only idea I want to reuse from the old design is placing industry jargon on the back of the card, just need a better way to present it. But if you have other ideas for the back--feel free to experiment.

Please use the colors complementary to the color we have on the website. Thank you!

```html
<!DOCTYPE html>
<html lang="en">
<head>
<meta charset="utf-8">
<title>QVR business card</title>
<link rel="stylesheet" href="https://fonts.googleapis.com/css2?family=Lato:wght@400;700&family=Montserrat:wght@700&family=Roboto+Condensed:wght@700&display=swap">
<style>
  :root{
    --backdrop:#e8e5e1;
    --card-white:#ffffff;
    --card-dark:#2a2a2c;
    --teal:#12b0ae;
    --teal-text:#1aab9c;
    --sand:#d9d39f;
    --white:#ffffff;
  }
  *{box-sizing:border-box;margin:0;padding:0}
  html,body{width:1138px;height:1200px;overflow:hidden;background:var(--backdrop)}
  .canvas{position:relative;width:1138px;height:1200px}

  .card{position:absolute;width:670px;height:382px;border-radius:16px;overflow:hidden;
        box-shadow:0 6px 14px rgba(0,0,0,.25)}
  .card--front{left:218px;top:198px;background:var(--card-white)}
  .card--back{left:216px;top:617px;background:var(--card-dark)}

  /* front */
  .brand{position:absolute;left:38px;top:58px;display:flex;align-items:center;gap:14px}
  .brand__dot{width:30px;height:30px;border-radius:50%;background:var(--teal)}
  .brand__name{font-family:"Lato",sans-serif;font-weight:700;font-size:40px;color:var(--teal);letter-spacing:.5px}

  .contact-band{position:absolute;left:0;top:221px;width:670px;height:131px}
  .contact-band > svg{position:absolute;inset:0}
  .contact{position:absolute;left:38px;top:16px;font-family:"Lato",sans-serif;color:var(--white)}
  .contact__name{font-weight:700;font-size:21px;margin-bottom:11px}
  .contact__line{display:flex;align-items:center;gap:8px;font-size:17.5px;line-height:23px}
  .contact__line svg{width:16px;height:16px;flex:none}

  /* back */
  .topics{position:absolute;left:30px;right:30px;top:24px;font-family:"Montserrat",sans-serif;font-weight:700;
          font-size:24px;line-height:40px;color:var(--teal-text);letter-spacing:1.5px;text-align:center;white-space:nowrap}
  .divider{position:absolute;left:60px;right:60px;top:284px;height:3px;background:var(--teal)}
  .tagline{position:absolute;left:0;right:0;top:298px;text-align:center;font-family:"Roboto Condensed",sans-serif;
           font-weight:700;font-size:42px;line-height:56px;letter-spacing:.5px;color:var(--white)}
</style>
</head>
<body>
<div class="canvas">

  <section class="card card--front">
    <div class="brand">
      <span class="brand__dot"></span>
      <span class="brand__name">Quorvane Studio</span>
    </div>

    <div class="contact-band">
      <svg width="670" height="131" viewBox="0 0 670 131" aria-hidden="true">
        <defs>
          <linearGradient id="bandFill" x1="0" y1="0" x2="0" y2="1">
            <stop offset="0" stop-color="#12b0ae"/>
            <stop offset="1" stop-color="#d9d39f"/>
          </linearGradient>
        </defs>
        <polygon points="0,0 560,0 540,131 0,131" fill="url(#bandFill)"/>
      </svg>
      <div class="contact">
        <p class="contact__name">Marcus Delvane</p>
        <p class="contact__line">
          <svg viewBox="0 0 16 16" aria-hidden="true"><path d="M4 1l3 3-2 2c1 2 3 4 5 5l2-2 3 3-2 2C7 14 2 9 2 3z" fill="#fff"/></svg>
          555-014-2297
        </p>
        <p class="contact__line">
          <svg viewBox="0 0 16 16" aria-hidden="true"><rect x="1" y="3" width="14" height="10" fill="none" stroke="#fff" stroke-width="1.6"/><path d="M1 3l7 6 7-6" fill="none" stroke="#fff" stroke-width="1.6"/></svg>
          mdelvane@quorvane.studio
        </p>
        <p class="contact__line">
          <svg viewBox="0 0 16 16" aria-hidden="true"><circle cx="8" cy="8" r="6.5" fill="none" stroke="#fff" stroke-width="1.4"/><ellipse cx="8" cy="8" rx="3" ry="6.5" fill="none" stroke="#fff" stroke-width="1.2"/><path d="M1.5 8h13M3 4.5h10M3 11.5h10" stroke="#fff" stroke-width="1.2"/></svg>
          www.quorvane.studio
        </p>
      </div>
    </div>
  </section>

  <section class="card card--back">
    <div class="topics">
      <p>STORYBOARDING · RAPID AUTHORING</p>
      <p>MICROLEARNING · ACCESSIBILITY</p>
      <p>VIDEO SCRIPTS · ASSESSMENTS</p>
      <p>LEARNER ANALYTICS</p>
      <p>SIMULATIONS · COACHING</p>
      <p>CURRICULUM MAPPING</p>
    </div>
    <div class="divider"></div>
    <p class="tagline">LET'S BUILD SOMETHING LEARNABLE</p>
  </section>

</div>
</body>
</html>
```